The Polish & Glow Studio Website Update

Hello. I am seeking to freshen up my website with a clean and easy feel that incorporates our modern chic style. Our services cater to mostly young professionals and modern moms.

We focus on natural nail care and gentle professional waxing. We are known for our cleanliness. Our clients like our current website, however I'm hoping to make it look even more professional and user friendly. Some clients have even said our current website feels welcoming, unlike other websites that in they feel give a snobbish vibe. I like clean lines, simple, fresh, and sometimes bold. Totally NOT a fan of whimsical.

I threw added an accent color to the color pallet...however it should be used in moderation. I am also open to other accent colors. I'd like the site to emphasize the Brazilian wax as much as nails, if not more than nail. The photos downloaded are just to give you a few images of who we are, however are not necessary. Current website www.thepolishandglowstudio.example

Target Market(s)

Females 30-55

Industry/Entity Type

Beauty Salon

Coding

Coded - Design and coding required

Number of Pages Required

5+ page

Font styles to use
Sans Serif

Colors
ffffff
1b1b1b
acd136
eeeeee
878787
c4c4c4
efefef
7f7f7f

Requirements
Must have
• Clean look
Nice to have
• Our logo
Should not have
• Whimsical

```html
<!DOCTYPE html>
<html lang="en">
<head>
<meta charset="utf-8">
<title>The Polish &amp; Glow Studio</title>
<link href="https://fonts.googleapis.com/css2?family=Open+Sans:wght@400;600;700&family=Raleway:wght@300;400;700&display=swap" rel="stylesheet">
<style>
:root{
  --white:#ffffff;
  --ink:#1b1b1b;
  --lime:#acd136;
  --mist:#eeeeee;
  --grey:#878787;
  --silver:#c4c4c4;
  --paper:#efefef;
  --ash:#7f7f7f;
  --bar:#2c2c2c;
  --red:#d0312d;
  --orange:#f0a020;
}
*{margin:0;padding:0;box-sizing:border-box}
html,body{width:1200px;height:2397px;overflow:hidden;background:var(--white)}
body{font-family:"Open Sans",Arial,sans-serif;color:var(--ink);position:relative}
a{color:inherit;text-decoration:none}

/* Header */
.site-header{height:99px;position:relative}
.call{position:absolute;left:100px;top:33px;display:flex;align-items:center;gap:10px;font-size:12px;color:var(--grey)}
.call strong{color:var(--ink);font-weight:400}
.call-icon{width:37px;height:37px;border:1px solid var(--silver);border-radius:50%;display:flex;align-items:center;justify-content:center}
.brand{position:absolute;left:0;right:0;top:34px;text-align:center;font-size:25px;font-weight:400;color:var(--ink);letter-spacing:.2px}
.btn{display:inline-flex;align-items:center;justify-content:center;background:var(--lime);color:var(--white);font-weight:700;font-size:12px;text-transform:uppercase;border-radius:2px}
.btn-schedule{position:absolute;left:946px;top:32px;width:156px;height:38px}

/* Navigation */
.main-nav{height:37px;background:var(--bar);display:flex;justify-content:space-between;align-items:center;padding:0 149px 0 149px}
.main-nav a{color:var(--white);font-size:11px;font-weight:600;text-transform:uppercase}

/* Hero */
.hero{position:relative;height:427px;background:linear-gradient(100deg,#3b3937 0%,#5c5855 35%,#6c6966 60%,#4a4744 100%)}
.hero-frame{position:absolute;left:300px;top:116px;width:600px;height:192px;border:3px solid var(--white);text-align:center;color:var(--white);font-family:"Raleway",sans-serif;font-weight:400;padding-top:26px}
.hero-frame .line{font-size:27px;line-height:38px;text-transform:uppercase}
.hero-frame b{font-weight:700}
.hero-frame .offer{font-size:45px;font-weight:300;line-height:60px;margin-top:4px}
.hero-frame .offer span{color:var(--lime)}
.dots{position:absolute;left:0;right:0;bottom:14px;display:flex;justify-content:center;gap:5px}
.dots i{width:6px;height:6px;border-radius:50%;background:var(--white)}
.dots i:first-child{background:var(--lime)}

/* Products */
.products{padding-top:53px;text-align:center}
.section-title{font-size:24px;font-weight:600;text-transform:uppercase;line-height:1.3}
.section-sub{font-size:14px;color:var(--ink);margin-top:8px}
.service-grid{display:grid;grid-template-columns:repeat(4,233px);column-gap:24px;row-gap:28px;margin:30px 0 0 99px;text-align:center}
.service-photo{height:214px}
.service-name{font-size:11px;font-weight:700;text-transform:uppercase;margin-top:20px}
.service-meta{font-size:13px;margin-top:6px}

/* Specials */
.specials{position:relative;margin:58px 0 0 99px;width:1003px;height:424px;background:radial-gradient(circle at 80% 40%,#f2d1b8 0%,#e5b495 18%,rgba(60,200,230,0) 40%),linear-gradient(120deg,#1ab4dc 0%,#49c8e8 45%,#9fe3f2 100%)}
.specials-brand{position:absolute;left:98px;top:82px;font-size:22px;color:var(--ink)}
.specials-title{position:absolute;left:131px;top:138px;font-size:33px;font-weight:700;color:var(--ink)}
.specials-offer{position:absolute;left:86px;top:187px;font-size:20px;font-weight:700;color:var(--ink);text-transform:uppercase}
.specials-offer span{color:var(--red)}
.specials-link{position:absolute;left:113px;top:221px;font-size:13px;font-weight:700;color:var(--ink);text-transform:uppercase}

/* Facials */
.facials{text-align:center;padding-top:58px}
.facials h2{font-size:22px;font-weight:600;text-transform:uppercase}
.facials p{font-size:14px;line-height:29px;width:740px;margin:18px auto 0}
.btn-book{width:142px;height:41px;margin-top:16px;font-size:13px}

/* Newsletter */
.newsletter{position:absolute;left:0;top:2049px;width:1200px;height:75px;background:var(--bar);display:flex;align-items:center;padding-left:100px}
.newsletter h3{color:var(--white);font-size:20px;font-weight:600;text-transform:uppercase}
.newsletter .hint{color:var(--grey);font-size:12px;margin-left:8px}
.email-field{position:absolute;left:593px;top:22px;width:377px;height:32px;background:var(--ink);border:1px solid #3c3c3c;color:var(--grey);font-size:11px;padding:8px 14px}
.btn-subscribe{position:absolute;left:978px;top:22px;width:121px;height:32px}

/* Footer */
.site-footer{position:absolute;left:0;top:2124px;width:1200px;height:273px;font-size:11px;line-height:24px}
.foot-col{position:absolute;top:40px}
.foot-col h4{font-size:11px;font-weight:700;text-transform:uppercase;line-height:18px;margin-bottom:6px}
.col-hours{left:99px;width:200px}
.col-hours .daily{color:var(--orange);font-weight:600}
.col-about{left:339px;width:300px}
.col-links{left:673px}
.col-links ul{list-style:none;display:grid;grid-template-columns:178px 100px}
.foot-brand{position:absolute;left:972px;top:88px;font-size:16px}
.foot-rule{position:absolute;left:99px;top:198px;width:1003px;height:1px;background:var(--mist)}
.copyright{position:absolute;left:0;right:0;top:220px;text-align:center;font-size:11px}
</style>
</head>
<body>

<header class="site-header">
  <div class="call">
    <span class="call-icon">
      <svg width="16" height="16" viewBox="0 0 24 24" fill="none" stroke="#878787" stroke-width="2"><path d="M22 16.9v3a2 2 0 0 1-2.2 2 19.8 19.8 0 0 1-8.6-3.1 19.5 19.5 0 0 1-6-6A19.8 19.8 0 0 1 2.1 4.2 2 2 0 0 1 4.1 2h3a2 2 0 0 1 2 1.7c.1 1 .4 1.9.7 2.8a2 2 0 0 1-.5 2.1L8 9.9a16 16 0 0 0 6 6l1.3-1.3a2 2 0 0 1 2.1-.5c.9.3 1.8.6 2.8.7a2 2 0 0 1 1.8 2z"/></svg>
    </span>
    <span>Call us : <strong>(555) 014-2938</strong></span>
  </div>
  <div class="brand">The Polish &amp; Glow Studio</div>
  <a class="btn btn-schedule" href="#">Schedule Online!</a>
</header>

<nav class="main-nav">
  <a href="#">Home</a>
  <a href="#">Schedule an Appointment</a>
  <a href="#">Products and Services</a>
  <a href="#">Careers</a>
  <a href="#">Specials</a>
  <a href="#">About Us</a>
  <a href="#">FAQ</a>
  <a href="#">Contact Us</a>
</nav>

<section class="hero" role="img" aria-label="Photo of the bright salon interior with manicure stations and nail polish shelves">
  <div class="hero-frame">
    <div class="line"><b>Facials</b> are now available at</div>
    <div class="line">the <b>Polish &amp; Glow</b> Studio</div>
    <div class="offer">UP TO <span>25% OFF</span></div>
  </div>
  <div class="dots"><i></i><i></i><i></i><i></i></div>
</section>

<section class="products">
  <h2 class="section-title">Products and Services</h2>
  <p class="section-sub">These best products choosen by our customers</p>
  <div class="service-grid">
    <div class="service"><div class="service-photo" role="img" aria-label="Photo of hands with a french manicure" style="background:linear-gradient(160deg,#f3e4dc,#d9a893)"></div><div class="service-name">Xpress Services</div><div class="service-meta">55 min, $70</div></div>
    <div class="service"><div class="service-photo" role="img" aria-label="Photo of a woman during a chemical peel treatment" style="background:linear-gradient(160deg,#f6ece6,#d8b3a0)"></div><div class="service-name">Chemical Peel</div><div class="service-meta">55 min, $70</div></div>
    <div class="service"><div class="service-photo" role="img" aria-label="Photo of a pedicure with pink orchids" style="background:linear-gradient(160deg,#f7f2f3,#e07ab8)"></div><div class="service-name">Xpress Manicure</div><div class="service-meta">55 min, $70</div></div>
    <div class="service"><div class="service-photo" role="img" aria-label="Photo of smooth legs after waxing" style="background:linear-gradient(160deg,#f8f4f1,#e3c2ad)"></div><div class="service-name">Wax</div><div class="service-meta">55 min, $70</div></div>
    <div class="service"><div class="service-photo" role="img" aria-label="Photo of a woman with glossy lips and an orchid" style="background:linear-gradient(160deg,#4b3226,#c98f7a)"></div><div class="service-name">Lips</div><div class="service-meta">55 min, $70</div></div>
    <div class="service"><div class="service-photo" role="img" aria-label="Photo of a woman with clear skin after a peel" style="background:linear-gradient(160deg,#f4d6dc,#d9a994)"></div><div class="service-name">Chemical Peel</div><div class="service-meta">55 min, $70</div></div>
    <div class="service"><div class="service-photo" role="img" aria-label="Photo of a relaxing facial massage" style="background:linear-gradient(160deg,#4f9a9c,#d8a98f)"></div><div class="service-name">Xpress Manicure</div><div class="service-meta">55 min, $70</div></div>
    <div class="service"><div class="service-photo" role="img" aria-label="Photo of manicured nails holding a pink flower" style="background:linear-gradient(160deg,#e98ca6,#f3d6cb)"></div><div class="service-name">Signature Manicure</div><div class="service-meta">55 min, $70</div></div>
  </div>
</section>

<section class="specials" role="img" aria-label="Photo of a woman sunbathing in a turquoise bikini on a bright blue background">
  <div class="specials-brand">The Polish &amp; Glow Studio</div>
  <div class="specials-title">SPECIALS</div>
  <div class="specials-offer">Up to <span>25% off</span> select services</div>
  <div class="specials-link">View the offer products</div>
</section>

<section class="facials">
  <h2>Facials are now available at the Polish &amp; Glow Studio</h2>
  <p>Our Signature Facial is meticulously customized to your skin's needs, be it quenching your skin's thirst, clearing unflattering breakouts, or repairing sun damage and fine lines</p>
  <a class="btn btn-book" href="#">Book Now!</a>
</section>

<section class="newsletter">
  <h3>Newsletter Signup</h3>
  <span class="hint">Get our recent updates through your email id</span>
  <div class="email-field">Enter your email id</div>
  <a class="btn btn-subscribe" href="#">Subscribe</a>
</section>

<footer class="site-footer">
  <div class="foot-col col-hours">
    <h4>Services by<br>appointment only</h4>
    <div>Appointments Available:</div>
    <div class="daily">Daily : 9am-8pm most days</div>
    <div style="line-height:18px">Salon is only staffed for scheduled appointments.</div>
  </div>
  <div class="foot-col col-about">
    <h4>Who we are</h4>
    <p>The Polish &amp; Glow Studio is a small nail spa located in Maple Grove, between Riverton and Lakeview. Our spa includes 1 private treatment room, 2 nail stations, and 2 pedicure stations.</p>
  </div>
  <div class="foot-col col-links">
    <h4>Welcome</h4>
    <ul>
      <li>Home</li><li>Specials</li>
      <li>Schedule An Appointment</li><li>About Us</li>
      <li>Products and Services</li><li>FAQ</li>
      <li>Careers</li><li>Contact Us</li>
    </ul>
  </div>
  <div class="foot-brand">The Polish &amp; Glow Studio</div>
  <div class="foot-rule"></div>
  <div class="copyright">Copyright 2016. The Polish &amp; Glow Studio. All rights reserved.</div>
</footer>

</body>
</html>
```